Home page design for my business

My business will be selling templated drive-in movie theater websites. I would like my business to state to my customers that they get a free website (with hosting fees) where they can take ticket sales digitally. My company will be called Reel-Lanternworks (for Drive In Movie Theatres).

Here are some websites of my potential customers:
https://www.pelorcrest.example/
https://moonglowcinemas.example/
https://oakridgeoutdoorscreen.example/

```html
<!DOCTYPE html>
<html lang="en">
<head>
<meta charset="utf-8">
<title>Reel-Lanternworks — Drive-In Theater Websites</title>
<link href="https://fonts.googleapis.com/css2?family=Montserrat:wght@500;600;700&family=Lato:wght@400;700&family=Great+Vibes&display=swap" rel="stylesheet">
<style>
:root{
  --accent:#e0105a;
  --black:#000;
  --panel:#111;
  --white:#fff;
}
*{box-sizing:border-box;margin:0;padding:0}
html,body{width:1200px;height:3706px;overflow:hidden;background:var(--black)}
body{font-family:'Lato',sans-serif;color:var(--white)}
.page{position:relative;width:1200px;height:3706px;overflow:hidden;background:var(--black)}
.abs{position:absolute}
.btn{position:absolute;display:flex;align-items:center;justify-content:center;background:var(--accent);color:var(--white);border-radius:24px;font-family:'Lato',sans-serif;font-weight:700;font-size:16px;letter-spacing:.2px}
.photo{position:absolute}

/* nav */
.site-nav{position:absolute;left:0;top:0;width:1200px;height:86px;background:var(--black)}
.brand{position:absolute;left:111px;top:28px;display:flex;align-items:center;gap:10px;font-family:'Montserrat',sans-serif;font-weight:700;font-size:21px;color:var(--white)}
.brand-mark{width:22px;height:22px;background:var(--accent)}
.nav-links{position:absolute;top:34px;left:531px;display:flex;gap:31px;font-family:'Montserrat',sans-serif;font-weight:600;font-size:15px}
.nav-links .active{color:var(--accent)}
.login{display:flex;align-items:center;gap:8px}

/* hero */
.hero{position:absolute;left:0;top:86px;width:1200px;height:609px;background:linear-gradient(180deg,#b58ee0 0%,#e9a9c6 16%,#f4d3b0 30%,#4f6d2f 48%,#365a22 70%,#2b461c 100%)}
.hero-title{position:absolute;left:0;width:1200px;top:50px;height:90px;line-height:90px;text-align:center;font-family:'Great Vibes',cursive;font-size:76px;color:var(--white)}
.circle-btn{position:absolute;border-radius:50%;background:rgba(0,0,0,.55);display:flex;align-items:center;justify-content:center}

/* about */
.about{position:absolute;left:0;top:695px;width:1200px;height:593px;background:linear-gradient(180deg,#0e0f13,#1b1d24 60%,#121318)}
.frame{position:absolute;border:9px solid var(--white)}
.section-title{font-family:'Montserrat',sans-serif;font-weight:700;font-size:39px}
.body-copy{font-size:14.5px;line-height:21.6px;color:#e8e8e8;text-align:justify}

/* rules */
.rules{position:absolute;left:0;top:1288px;width:1200px;height:611px;background:var(--panel)}
.rule{position:absolute;left:111px;width:455px;display:flex;gap:13px;font-size:14.5px;line-height:21.6px;color:#e8e8e8;text-align:justify}
.rule-dot{flex:none;width:18px;height:18px;margin-top:2px;border-radius:50%;border:2px solid var(--accent);background:var(--white);box-shadow:inset 0 0 0 3px var(--white),inset 0 0 0 9px var(--accent)}

/* photos */
.plus{position:absolute;left:832px;top:2215px;width:80px;height:80px;border-radius:50%;background:var(--accent);display:flex;align-items:center;justify-content:center}

/* showing */
.closed{position:absolute;left:0;width:1200px;top:2546px;text-align:center;font-family:'Montserrat',sans-serif;font-weight:700;font-size:37px;line-height:43px}
.now-showing{position:absolute;left:0;width:1200px;top:2652px;text-align:center;font-family:'Montserrat',sans-serif;font-weight:700;font-size:41px;color:var(--accent);text-shadow:0 0 10px rgba(224,16,90,.8)}
.caption{position:absolute;top:3142px;width:311px;text-align:center;font-family:'Montserrat',sans-serif;font-weight:700;font-size:19px}

/* footer */
.site-footer{position:absolute;left:0;top:3263px;width:1200px;height:443px;background:var(--panel)}
.foot-col{position:absolute;top:94px}
.foot-col h4{font-family:'Montserrat',sans-serif;font-weight:700;font-size:19px;padding-bottom:18px;width:140px;border-bottom:1px solid #aaa;white-space:nowrap}
.foot-list{list-style:none;margin-top:28px;font-size:13px;line-height:21.5px;color:#e5e5e5}
.contact-row{display:flex;align-items:center;gap:12px;font-size:13px;line-height:20px;color:#e5e5e5}
.icon-disc{flex:none;width:34px;height:34px;border-radius:50%;background:var(--white);display:flex;align-items:center;justify-content:center}
.copyright{position:absolute;left:0;top:3624px;width:1200px;text-align:center;font-size:14px;color:#e5e5e5}
</style>
</head>
<body>
<div class="page">

  <header class="site-nav">
    <div class="brand"><span class="brand-mark"></span>Reel-Lanternworks</div>
    <nav class="nav-links">
      <span class="active">Home</span><span>About</span><span>Theater Rules</span><span>Photos</span><span>Contact</span>
      <span class="login">
        <svg width="24" height="24" viewBox="0 0 24 24"><circle cx="12" cy="12" r="11" fill="none" stroke="#e0105a" stroke-width="2"/><circle cx="12" cy="9" r="4" fill="#e0105a"/><path d="M5 19c2-4 12-4 14 0" fill="#e0105a"/></svg>Login
      </span>
    </nav>
  </header>

  <section class="hero" role="img" aria-label="Aerial view at sunset of a drive-in theater clearing with parked cars facing a screen, surrounded by trees">
    <div class="hero-title">Reel-Lanternworks</div>
    <div class="btn" style="left:518px;top:150px;width:164px;height:43px">GET STARTED</div>
    <div class="circle-btn" style="left:68px;top:302px;width:46px;height:46px">
      <svg width="12" height="12" viewBox="0 0 12 12"><path d="M8 2 4 6l4 4" stroke="#fff" stroke-width="1.6" fill="none"/></svg>
    </div>
    <div class="circle-btn" style="left:1083px;top:302px;width:46px;height:46px">
      <svg width="12" height="12" viewBox="0 0 12 12"><path d="M4 2l4 4-4 4" stroke="#fff" stroke-width="1.6" fill="none"/></svg>
    </div>
  </section>
  <div class="circle-btn" style="left:574px;top:669px;width:52px;height:52px;background:#000;z-index:2">
    <svg width="22" height="34" viewBox="0 0 22 34"><path d="M11 2v28M3 22l8 9 8-9" stroke="#fff" stroke-width="2" fill="none"/></svg>
  </div>

  <section class="about">
    <div class="frame photo" style="left:232px;top:72px;width:344px;height:399px;background:linear-gradient(160deg,#3a3c46,#1c1d24 60%,#2a2b32)" role="img" aria-label="Close-up of a vintage film projector lens in a dark room"></div>
    <div class="frame photo" style="left:94px;top:200px;width:171px;height:157px;background:linear-gradient(180deg,#3b4a66,#1f2633)" role="img" aria-label="Inside a classic car at the drive-in"></div>
    <div class="frame photo" style="left:145px;top:325px;width:311px;height:193px;background:linear-gradient(180deg,#7a7a7a,#3a3a3a 55%,#6a2a2a)" role="img" aria-label="Miniature model of a drive-in with toy cars facing a screen"></div>
    <h2 class="section-title abs" style="left:616px;top:72px">About us</h2>
    <p class="body-copy abs" style="left:616px;top:134px;width:475px">Reel-Lanternworks builds ready-made websites for drive-in movie theaters. Every theater that joins us gets a free website, with hosting fees covered, built on a template designed for outdoor screens. Your guests can buy tickets digitally from any phone or computer, pick a showtime, reserve a car spot and pay online before they arrive. You manage films, prices and show nights from one simple dashboard, with no code and no setup costs. Post your titles and keep your gallery fresh.</p>
    <p class="body-copy abs" style="left:616px;top:329px;width:475px">Choose a template, add your theater name and photos, and go live in days. We handle the hosting, security and updates, so you can focus on the screen. Digital ticket sales arrive straight in your account, and every sale is tracked so you always know how many cars are coming each night of the season.</p>
    <div class="btn" style="left:616px;top:463px;width:163px;height:44px">LEARN MORE</div>
  </section>

  <section class="rules">
    <h2 class="section-title abs" style="left:111px;top:50px">Theater Rules</h2>
    <div class="rule" style="top:115px"><span class="rule-dot"></span><span>Lorem ipsum dolor sit amet, consectetur adipiscing elit, sed do eiusmod tempor incididunt ut labore et dolore magna aliqua.</span></div>
    <div class="rule" style="top:180px"><span class="rule-dot"></span><span>Ut enim ad minim veniam, quis nostrud exercitation ullamco laboris nisi ut aliquip ex ea commodo consequat.</span></div>
    <div class="rule" style="top:244px"><span class="rule-dot"></span><span>Duis aute irure dolor in reprehenderit in voluptate velit esse cillum dolore eu fugiat nulla pariatur.</span></div>
    <div class="rule" style="top:309px"><span class="rule-dot"></span><span>Excepteur sint occaecat cupidatat non proident, sunt in culpa qui officia deserunt mollit anim id est laborum.</span></div>
    <div class="rule" style="top:373px"><span class="rule-dot"></span><span>Lorem ipsum dolor sit amet, consectetur adipiscing elit, sed do eiusmod tempor incididunt ut labore et dolore magna aliqua.</span></div>
    <div class="rule" style="top:438px"><span class="rule-dot"></span><span>Ut enim ad minim veniam, quis nostrud exercitation ullamco laboris nisi ut aliquip ex ea commodo consequat.</span></div>
    <div class="btn" style="left:111px;top:511px;width:162px;height:41px">LEARN MORE</div>
    <div class="photo" style="left:601px;top:0;width:599px;height:611px;background:linear-gradient(180deg,#3a4a5a 0%,#2a2f36 30%,#141518 60%,#0c0c0e 100%)" role="img" aria-label="View from a car dashboard toward a blurred drive-in screen"></div>
  </section>

  <section>
    <h2 class="section-title abs" style="left:0;width:1200px;text-align:center;top:1972px">Photos</h2>
    <div class="photo" style="left:105px;top:2042px;width:262px;height:204px;background:linear-gradient(180deg,#c9d3de,#8a9099 55%,#55585e)" role="img" aria-label="Parking lot with cars in front of a large outdoor screen"></div>
    <div class="photo" style="left:381px;top:2042px;width:262px;height:204px;background:linear-gradient(180deg,#b9c4d4,#4d6f9a 55%,#2c3a4f)" role="img" aria-label="Staff in protective gear attending cars at an entry"></div>
    <div class="photo" style="left:105px;top:2263px;width:262px;height:205px;background:linear-gradient(180deg,#c8cdd4,#6f6f72 55%,#4d4a48)" role="img" aria-label="Hands holding a popcorn bucket beside a car at the screen"></div>
    <div class="photo" style="left:381px;top:2263px;width:262px;height:205px;background:linear-gradient(180deg,#9aa6c6,#5a6180 55%,#3b3f52)" role="img" aria-label="Evening drive-in lot with a bright white screen"></div>
    <div class="photo" style="left:656px;top:2042px;width:433px;height:426px;background:linear-gradient(180deg,#b7c4d6,#8e96a3 45%,#5e5851 75%,#3c3834)" role="img" aria-label="Empty drive-in screen at dusk with a car and speaker post"></div>
    <div class="plus"><svg width="26" height="26" viewBox="0 0 26 26"><path d="M13 2v22M2 13h22" stroke="#fff" stroke-width="3"/></svg></div>
  </section>

  <section>
    <h2 class="closed">CLOSED FOR THE SEASON.<br>THANK YOU FOR SUPPORTING US!</h2>
    <h2 class="now-showing">Now Showing</h2>
    <div class="photo" style="left:111px;top:2724px;width:311px;height:403px;background:linear-gradient(180deg,#1e2a35,#2e4a48 55%,#1d2d2c)" role="img" aria-label="Horror night movie poster"></div>
    <div class="photo" style="left:445px;top:2724px;width:310px;height:403px;background:linear-gradient(180deg,#3a4c6e,#1e2a44 55%,#10141e)" role="img" aria-label="Superhero movie poster"></div>
    <div class="photo" style="left:778px;top:2724px;width:311px;height:403px;background:linear-gradient(180deg,#1a1c22,#3a3d44 45%,#0e0f12)" role="img" aria-label="Dark superhero movie teaser poster"></div>
    <div class="caption" style="left:111px">Movie Preview</div>
    <div class="caption" style="left:444px">Movie Preview</div>
    <div class="caption" style="left:778px">Movie Preview</div>
  </section>

  <footer class="site-footer">
    <div class="foot-col" style="left:111px">
      <h4>Follow us</h4>
      <div class="contact-row" style="margin-top:34px">
        <span class="icon-disc"><svg width="16" height="18" viewBox="0 0 16 18"><path d="M8 1a6 6 0 0 0-6 6c0 4.5 6 10 6 10s6-5.5 6-10a6 6 0 0 0-6-6z" fill="#e0105a"/><circle cx="8" cy="7" r="2.2" fill="#fff"/></svg></span>
        <span>Lorem ipsum dolor sit amet,<br>consectetur</span>
      </div>
      <div class="contact-row" style="margin-top:14px">
        <span class="icon-disc"><svg width="16" height="16" viewBox="0 0 16 16"><path d="M3 1h3l1.5 4-2 1.2a9 9 0 0 0 4.3 4.3L11 8.5l4 1.5v3a2 2 0 0 1-2 2A12 12 0 0 1 1 3a2 2 0 0 1 2-2z" fill="#e0105a"/></svg></span>
        <span>+1 555 014 2288</span>
      </div>
      <div class="contact-row" style="margin-top:10px">
        <span class="icon-disc"><svg width="16" height="12" viewBox="0 0 16 12"><rect width="16" height="12" rx="1.5" fill="#e0105a"/><path d="M1 1.5 8 7l7-5.5" stroke="#fff" stroke-width="1.4" fill="none"/></svg></span>
        <span>info@reellanternworks.example</span>
      </div>
    </div>
    <div class="foot-col" style="left:445px">
      <h4>Find Out More</h4>
      <ul class="foot-list"><li>Home</li><li>Food Menu</li><li>FAQ</li><li>Theater Rules</li><li>Photos</li><li>Contact Us</li></ul>
    </div>
    <div class="foot-col" style="left:694px">
      <h4>Quick links</h4>
      <ul class="foot-list"><li>Privacy Policy</li><li>Terms &amp; Condition</li><li>Faq</li><li>Support</li><li>Gallery</li><li>Contact</li></ul>
    </div>
    <div class="foot-col" style="left:947px">
      <h4>Follow us</h4>
      <div class="contact-row" style="margin-top:36px"><span class="icon-disc"></span><span>Friendsboard</span></div>
      <div class="contact-row" style="margin-top:9px"><span class="icon-disc"></span><span>Careerlinkup</span></div>
    </div>
  </footer>
  <div class="copyright">© 2022 Company name.All Rights Reserved &nbsp;| Privacy Policy | &nbsp;Terms</div>

</div>
</body>
</html>
```